Additional Benefits of Working for VELMAR

Please prepare an infographic on the additional benefits besides salary of working at VELMAR as detailed in the attached word document. Also attached is our logo in eps and our company design "Grounds". We are a Not For Profit company that finds jobs for unemployed people of government benefit payments

Target Market(s)

Attracting people to work for VELMAR. Making VELMAR an employer of choice.

Font styles to use
Sans Serif

Colors

Designer to choose colors to be used in the design.

Requirements
Must have
• be on 1 page
• have our logo
Nice to have
• Our Grounds design worked into it.
• Happy engaged employees
• Community engagement - we are a not for profit organisation
Should not have
• Discrimination, swearing,

```html
<!DOCTYPE html>
<html lang="en">
<head>
<meta charset="utf-8">
<title>VELMAR – Benefits of Working with Us</title>
<link href="https://fonts.googleapis.com/css2?family=Questrial&display=swap" rel="stylesheet">
<style>
:root{
  --teal:#168a6f;
  --teal-dark:#0e6b55;
  --teal-light:#23a383;
  --gold:#c8923a;
  --gold-light:#e7b867;
  --gold-text:#e9b760;
  --ink:#1f1f1f;
  --panel:#c9c9cc;
  --white:#ffffff;
  --page:#ffffff;
}
*{box-sizing:border-box;margin:0;padding:0}
html,body{width:1200px;height:990px;overflow:hidden;background:var(--page)}
body{font-family:"Questrial",sans-serif;color:var(--ink)}
.stage{position:absolute;left:78px;top:8px;width:841px;height:785px;transform:scale(1.24);transform-origin:0 0}
.grounds{position:absolute;inset:0;
  background:
    radial-gradient(ellipse 260px 200px at 75% 65%,rgba(240,214,170,.75),transparent 70%),
    radial-gradient(ellipse 240px 260px at 20% 40%,rgba(200,230,210,.6),transparent 70%),
    radial-gradient(ellipse 220px 180px at 90% 20%,rgba(190,225,200,.55),transparent 70%),
    radial-gradient(ellipse 200px 160px at 55% 90%,rgba(215,235,205,.6),transparent 70%),
    var(--panel);
  box-shadow:6px 6px 8px rgba(0,0,0,.35)}
.logo-badge{position:absolute;left:10px;top:7px;width:218px;height:82px;border-radius:50%;background:var(--white);
  display:flex;align-items:center;justify-content:center}
.logo-name{font-size:44px;font-weight:400;color:#111;letter-spacing:-1px}
.title-banner{position:absolute;left:256px;top:25px;width:540px;height:72px;border-radius:18px;
  background:linear-gradient(180deg,var(--teal-light),var(--teal-dark));
  display:flex;align-items:center;justify-content:center;box-shadow:0 2px 3px rgba(0,0,0,.25)}
.title-banner h1{font-weight:400;font-size:38px;color:var(--gold-text);letter-spacing:.5px}
.connectors{position:absolute;inset:0}
.icon-ring{position:absolute;width:84px;height:84px;border-radius:50%;background:var(--white);
  border:4px solid var(--teal);display:flex;align-items:center;justify-content:center}
.icon-ring svg{width:50px;height:50px;fill:none;stroke:var(--teal);stroke-width:2.4;stroke-linecap:round;stroke-linejoin:round}
.card{position:absolute;width:180px;border:4px solid var(--gold);border-radius:14px;background:var(--white);
  box-shadow:0 2px 3px rgba(0,0,0,.2)}
.card-head{background:linear-gradient(180deg,var(--gold-light),var(--gold));color:var(--teal-dark);border-radius:10px 10px 0 0;
  text-align:center;font-size:16px;font-weight:400;line-height:18px;padding:6px 4px 5px}
.card-body{list-style:none;padding:6px 6px 5px;font-size:9.2px;line-height:13px;letter-spacing:-.1px;text-align:justify}
.card-body li{margin-bottom:4px}
.card-body li:last-child{margin-bottom:0}
.card-body li::before{content:"• "}
</style>
</head>
<body>
<main class="stage">
  <div class="grounds" role="img" aria-label="Company Grounds design: flowing organic pattern in soft greens, sand and peach over grey"></div>

  <div class="logo-badge"><span class="logo-name">velmar</span></div>
  <div class="title-banner"><h1>Benefits of Working with Us</h1></div>

  <svg class="connectors" viewBox="0 0 841 785" width="841" height="785" aria-hidden="true">
    <g stroke="#168a6f" stroke-width="4" fill="none">
      <line x1="111" y1="138" x2="705" y2="138"/>
      <line x1="108" y1="485" x2="706" y2="485"/>
      <line x1="200" y1="305" x2="620" y2="305"/>
      <line x1="200" y1="619" x2="620" y2="619"/>
      <line x1="111" y1="152" x2="111" y2="210"/>
      <line x1="301" y1="152" x2="301" y2="212"/>
      <line x1="505" y1="152" x2="505" y2="212"/>
      <line x1="705" y1="152" x2="705" y2="216"/>
      <line x1="108" y1="440" x2="108" y2="566"/>
      <line x1="706" y1="398" x2="706" y2="566"/>
      <line x1="300" y1="497" x2="300" y2="564"/>
      <line x1="505" y1="497" x2="505" y2="566"/>
    </g>
  </svg>

  <div class="icon-ring" style="left:69px;top:110px"><svg viewBox="0 0 50 50"><line x1="25" y1="8" x2="25" y2="42"/><line x1="10" y1="16" x2="40" y2="16"/><circle cx="25" cy="8" r="2.5"/><path d="M10 16 4 30h12z"/><path d="M40 16 34 30h12z"/><path d="M4 30a6 4 0 0 0 12 0M34 30a6 4 0 0 0 12 0"/><line x1="17" y1="42" x2="33" y2="42"/></svg></div>
  <div class="icon-ring" style="left:259px;top:110px"><svg viewBox="0 0 50 50"><path d="M25 41 9 25a9 9 0 0 1 16-12 9 9 0 0 1 16 12z"/><path d="M25 36 13 24a6 6 0 0 1 12-8 6 6 0 0 1 12 8z"/></svg></div>
  <div class="icon-ring" style="left:463px;top:110px"><svg viewBox="0 0 50 50"><rect x="6" y="6" width="38" height="38"/><polyline points="10,38 18,28 24,32 34,18 40,12"/><polyline points="33,12 40,12 40,19"/><line x1="14" y1="44" x2="14" y2="34"/><line x1="22" y1="44" x2="22" y2="32"/><line x1="30" y1="44" x2="30" y2="26"/><line x1="38" y1="44" x2="38" y2="20"/></svg></div>
  <div class="icon-ring" style="left:663px;top:110px"><svg viewBox="0 0 50 50"><rect x="8" y="10" width="34" height="30" rx="3"/><line x1="8" y1="17" x2="42" y2="17"/><rect x="28" y="22" width="14" height="10" rx="2"/><circle cx="34" cy="27" r="1.5"/></svg></div>

  <div class="icon-ring" style="left:66px;top:455px"><svg viewBox="0 0 50 50"><circle cx="25" cy="25" r="18"/><path d="M14 14c4 3 6 6 4 10s2 8 6 9M30 8c-2 5 2 7 6 7s4 6 2 10"/></svg></div>
  <div class="icon-ring" style="left:258px;top:455px"><svg viewBox="0 0 50 50"><polyline points="4,10 11,10 16,32 38,32 43,15 13,15"/><line x1="20" y1="15" x2="21" y2="32"/><line x1="28" y1="15" x2="28" y2="32"/><line x1="36" y1="15" x2="35" y2="32"/><line x1="15" y1="23" x2="41" y2="23"/><circle cx="19" cy="40" r="3"/><circle cx="35" cy="40" r="3"/></svg></div>
  <div class="icon-ring" style="left:463px;top:455px"><svg viewBox="0 0 50 50"><path d="M15 5h20v12l-10 6-10-6z"/><line x1="25" y1="5" x2="25" y2="23"/><circle cx="25" cy="33" r="11"/><path d="M25 27l2 4 4 .5-3 3 .8 4-3.8-2-3.8 2 .8-4-3-3 4-.5z"/></svg></div>
  <div class="icon-ring" style="left:664px;top:455px"><svg viewBox="0 0 50 50"><path d="M25 38V22"/><path d="M25 24c-2-8-10-10-16-8 2 7 9 10 16 8z"/><path d="M25 22c2-9 10-13 18-11-2 8-10 12-18 11z"/><path d="M8 42c2-6 8-6 10-4 3-4 11-4 14 0 3-2 8-1 10 4z"/></svg></div>

  <section class="card" style="left:21px;top:207px;min-height:235px">
    <h2 class="card-head">Life Balance</h2>
    <ul class="card-body">
      <li>VELMAR Day Leave. An extra day of at Christmas</li>
      <li>BIRTHDAY Leave. A paid day off on your birthday</li>
      <li>A day off every month as Time in Lieu</li>
      <li>4 weeks Annual Leave</li>
      <li>Genereous Personal Leave</li>
      <li>Support for parental leave for the birth or adoption of a child</li>
      <li>Flexible work arrangements</li>
    </ul>
  </section>
  <section class="card" style="left:218px;top:209px;min-height:208px">
    <h2 class="card-head">Wellbeing</h2>
    <ul class="card-body">
      <li>Up to $450 per year to spend on Wellbeing services such as gym or yoga memberships</li>
      <li>Free counselling services 24x7 via our Employee Assistance Program</li>
      <li>Discount private health insurance</li>
      <li>WHS policies which suppor a safe, inclusive work place</li>
    </ul>
  </section>
  <section class="card" style="left:417px;top:209px;min-height:228px">
    <h2 class="card-head">Career Growth<br>&amp;Professional<br>Development</h2>
    <ul class="card-body">
      <li>Ongoing internal training and development opportunities</li>
      <li>External srudy support § study leave</li>
      <li>Access to the tools and technology to do your job well</li>
      <li>Career advancement opportunities</li>
      <li>Internal job vacancy listing</li>
    </ul>
  </section>
  <section class="card" style="left:617px;top:213px;min-height:187px">
    <h2 class="card-head">Remuneration<br>&amp; Salary Packaging</h2>
    <ul class="card-body">
      <li>Competetive salary</li>
      <li>Ability to salary package up to $15,900 and reduce your tax. Package rent, home loans, child care and much more</li>
      <li>Salary package up to $2,650 on meal entertainment and holiday accommodation</li>
    </ul>
  </section>

  <section class="card" style="left:19px;top:563px;min-height:156px">
    <h2 class="card-head">Diversity &amp; Inclusion</h2>
    <ul class="card-body">
      <li>An inclusive and diverse culture where different backgounds, experiences and perspectives are valued</li>
      <li>Gender diversity. Over 50% of our workforce and our leaders are female</li>
    </ul>
  </section>
  <section class="card" style="left:216px;top:561px;min-height:193px">
    <h2 class="card-head">Benefits</h2>
    <ul class="card-body">
      <li>Discounted vouchers for Harvest Mart, Greenfield Grocers, Voltline, Starlight Cinemas, Cellar Lane, ValueHub, Outdoor Depot and many others via Paywise e-wallet</li>
      <li>A range of other employee discounts are also available, including access to discounted bankin and finance, vehicle purchasing, leasing and hotel accomodation</li>
    </ul>
  </section>
  <section class="card" style="left:417px;top:563px;min-height:112px">
    <h2 class="card-head">Recognition</h2>
    <ul class="card-body">
      <li>We celebrate our people foreaching service milestones</li>
      <li>Team &amp; individual recognition for high performance</li>
    </ul>
  </section>
  <section class="card" style="left:617px;top:563px;min-height:186px">
    <h2 class="card-head">Contributing to<br>Community</h2>
    <ul class="card-body">
      <li>Team involvement in local charity and community events</li>
      <li>Participation in VELMAR's 1000 Jobs in 100 days</li>
      <li>Strong relationships and connection with Indigenous Communities in support of Indigenous Emplyment</li>
    </ul>
  </section>
</main>
</body>
</html>
```